AI Business Tools Landing Page

My web-based website builder (Pavlora.com) will be adding many new features in the very near future and I need an eye-catching landing page to promote these new products.

The page will have a primary section of the 8 main products we are promoting:
1. AI Instant Website Generator
2. AI Chatbot
3. Online Store Builder with AI Assistance
4. AI Auto-Blogging System
5. Online Scheduling System
6. Custom Email System
7. SEO Service
8. CRM System

The page will also have a smaller section for links to our affiliate programs. These can be smaller, less-promanent buttons or links. These are the affiliate products:
1. Get Your LLC
2. Website Design and Maintenance
3. Search Ads Management
4. Social Media Posting Service
5. Logo Design
6. Trademark Registration
7. Patent Application
8. Printing Services (including postcards, flyers, and merch.)
9. Bulk AI Content Generator

The theme and color scheme of the page should follow the theme of our main website, which is https://pavlora.com.

I need the page fully coded and ready to deploy on my server.

I look forward to seeing your amazing designs!

```html
<!DOCTYPE html>
<html lang="en">
<head>
<meta charset="utf-8">
<title>Pavlora – Additional Features &amp; Tools for Website</title>
<link rel="stylesheet" href="https://fonts.googleapis.com/css2?family=Poppins:wght@300;400;500;600;700&display=swap">
<style>
  :root{
    --navy:#0b1a3d;
    --navy-deep:#061233;
    --footer:#0e2442;
    --cyan:#29b8f0;
    --cyan-bright:#1ea7f5;
    --cyan-soft:#dff2fb;
    --ink:#121a2e;
    --line:#cfe6f3;
    --white:#ffffff;
  }
  *{box-sizing:border-box;margin:0;padding:0}
  html,body{width:1200px;height:2182px;overflow:hidden;background:var(--white)}
  body{font-family:"Poppins",sans-serif;color:var(--ink);position:relative}

  /* Hero */
  .hero{position:absolute;left:0;top:0;width:1200px;height:670px;overflow:hidden}
  .hero-art{position:absolute;inset:0;
    background:radial-gradient(ellipse 60% 55% at 50% 30%,#12349a 0%,#0a1f66 45%,transparent 75%),
               radial-gradient(ellipse 90% 40% at 50% 95%,#1d7fb8 0%,#0c3f7a 40%,transparent 80%),
               linear-gradient(180deg,#040c2a 0%,#071845 55%,#0b2f66 100%)}
  .hero-edge{position:absolute;left:0;top:0}
  .brand{display:flex;align-items:center;gap:10px;font-weight:600;color:var(--white)}
  .brand-dot{width:26px;height:26px;border-radius:50%;background:var(--cyan)}
  .hero .brand{position:absolute;left:0;right:0;top:180px;justify-content:center;font-size:36px}
  .hero-title{position:absolute;left:0;right:0;top:238px;text-align:center;line-height:1.18}
  .hero-title .strong{display:block;font-size:49px;font-weight:700;color:var(--white)}
  .hero-title .light{display:block;font-size:49px;font-weight:400;color:var(--cyan)}

  /* Section headings */
  .section-heading{position:absolute;left:0;right:0;text-align:center;font-size:33px;font-weight:400;color:var(--ink)}
  .section-heading b{font-weight:700}
  .section-heading::after{content:"";display:block;width:76px;height:3px;background:var(--cyan);margin:9px auto 0}

  /* Features grid */
  .features{position:absolute;left:93px;top:773px;width:1019px;display:grid;
    grid-template-columns:509px 510px;grid-template-rows:180px 179px 181px 195px}
  .feature{position:relative;padding:31px 10px 0 123px}
  .feature:nth-child(even){padding-left:113px;border-left:2px solid var(--line)}
  .feature:nth-child(-n+6){border-bottom:2px solid var(--line)}
  .feature:nth-child(odd){margin-right:6px}
  .feature-icon{position:absolute;left:40px;top:34px;width:62px;height:62px;border-radius:50%;
    background:linear-gradient(150deg,#5fd3f7,#14a2ec);
    box-shadow:0 0 0 5px #fff,0 0 0 6px #bfe6f7,0 4px 10px rgba(20,150,220,.25);
    display:flex;align-items:center;justify-content:center}
  .feature:nth-child(even) .feature-icon{left:32px}
  .feature-title{font-size:15.5px;font-weight:600;text-transform:uppercase;line-height:1.25;color:var(--ink);margin-bottom:14px}
  .feature ul{list-style:none}
  .feature li{position:relative;font-size:11.6px;line-height:1.2;padding-left:19px;margin-bottom:19px;color:var(--ink);white-space:nowrap}
  .feature li::before{content:"";position:absolute;left:2px;top:3px;width:5px;height:5px;
    border-right:2px solid var(--cyan);border-top:2px solid var(--cyan);transform:rotate(45deg)}

  /* Tools */
  .tools{position:absolute;left:0;top:1581px;width:1200px;height:484px;
    background:linear-gradient(135deg,#e4f3fb 0%,#eef8fc 50%,#dcf1fa 100%)}
  .tools-notch{position:absolute;left:550px;top:0}
  .tool-grid{position:absolute;left:184px;top:141px;display:grid;grid-template-columns:274px 274px 274px;
    grid-auto-rows:72px;column-gap:14px;row-gap:10px}
  .tool{display:flex;flex-direction:column;align-items:center;justify-content:center;text-align:center;
    background:var(--white);border:2px solid var(--line);border-radius:3px;
    font-size:16px;font-weight:500;color:var(--navy);text-decoration:none;line-height:1.2}
  .tool small{font-size:9px;font-weight:400;color:#555;margin-top:4px}
  .tool.is-featured{background:linear-gradient(90deg,#3cc6f2,#17a6f7);border-color:transparent;color:var(--white)}

  /* Footer */
  .site-footer{position:absolute;left:0;top:2065px;width:1200px;height:117px;background:var(--footer)}
  .site-footer .brand{position:absolute;left:113px;top:38px;font-size:33px}
  .copyright{position:absolute;left:0;right:0;top:49px;text-align:center;font-size:15px;color:#e8eef6;padding-left:10px}
  .social{position:absolute;left:893px;top:36px;display:grid;grid-template-columns:repeat(5,22px);column-gap:15px;row-gap:13px}
  .social span{width:22px;height:22px;border-radius:50%;background:var(--white)}
</style>
</head>
<body>

<header class="hero">
  <div class="hero-art" role="img" aria-label="Glowing blue digital network globe with connected points"></div>
  <svg class="hero-edge" width="1200" height="670" viewBox="0 0 1200 670" aria-hidden="true">
    <polygon points="0,657 652,603 1200,665 1200,670 0,670" fill="#ffffff"/>
    <polygon points="652,603 1200,559 1200,665" fill="#29b8f0"/>
  </svg>
  <div class="brand"><span class="brand-dot"></span>Pavlora</div>
  <h1 class="hero-title"><span class="strong">Additional Features</span><span class="light">&amp; Tools for Website</span></h1>
</header>

<h2 class="section-heading" style="top:680px">Additional Features <b>for Your Website</b></h2>

<section class="features">
  <article class="feature">
    <div class="feature-icon"><svg width="30" height="30" viewBox="0 0 30 30" fill="none" stroke="#fff" stroke-width="2"><rect x="4" y="5" width="22" height="17" rx="2"/><path d="M8 11h8M8 15h6M11 26h8"/></svg></div>
    <h3 class="feature-title">AI Instant Website Generator</h3>
    <ul>
      <li>Get a professional, SEO-optimized website in seconds!</li>
      <li>Includes custom domain, secure high-speed hosting,<br>professional images, and more!</li>
    </ul>
  </article>
  <article class="feature">
    <div class="feature-icon"><svg width="30" height="30" viewBox="0 0 30 30" fill="none" stroke="#fff" stroke-width="2"><rect x="5" y="7" width="20" height="14" rx="4"/><path d="M10 21l-3 5M11 14h1M18 14h1"/></svg></div>
    <h3 class="feature-title">AI Chatbot</h3>
    <ul>
      <li>Fully-trainable ChatBot will learn about your business to<br>automate the customer support process!</li>
      <li>Built-in CRM features integrate emailing, text<br>messaging, and contact forms!</li>
    </ul>
  </article>
  <article class="feature">
    <div class="feature-icon"><svg width="30" height="30" viewBox="0 0 30 30" fill="none" stroke="#fff" stroke-width="2"><rect x="4" y="5" width="22" height="17" rx="2"/><path d="M9 11h12l-2 6h-8z"/></svg></div>
    <h3 class="feature-title">Online Store Builder (E-Commerce)<br>with AI Assistance</h3>
    <ul>
      <li>Sell you products online and integrate your products<br>into any website!</li>
      <li>Accept payments from multiple payment gateways<br>including Payvia and Cashlane!</li>
    </ul>
  </article>
  <article class="feature">
    <div class="feature-icon"><svg width="30" height="30" viewBox="0 0 30 30" fill="none" stroke="#fff" stroke-width="2"><rect x="6" y="4" width="16" height="22" rx="2"/><path d="M10 10h8M10 14h8M10 18h5"/></svg></div>
    <h3 class="feature-title">AI Auto-Blogging System</h3>
    <ul>
      <li>AI will generate an incredible blog for your business in<br>seconds and immediately begin posting content for you!</li>
      <li>Choose from daily, weekly, or monthly automated blog<br>posting. Consistent, unique, SEO-optimized content<br>posting on cruise control!</li>
    </ul>
  </article>
  <article class="feature">
    <div class="feature-icon"><svg width="30" height="30" viewBox="0 0 30 30" fill="none" stroke="#fff" stroke-width="2"><rect x="5" y="6" width="20" height="16" rx="2"/><path d="M10 3v5M20 3v5M9 13h2M14 13h2M19 13h2M9 17h2M14 17h2"/></svg></div>
    <h3 class="feature-title">Online Scheduling System</h3>
    <ul>
      <li>Get appointment bookings, restaurant reservations, or<br>consultations scheduled directly from your website!</li>
      <li>Manage your employees' schedules and all your<br>appointments from a simple, user-friendly dashboard!</li>
    </ul>
  </article>
  <article class="feature">
    <div class="feature-icon"><svg width="30" height="30" viewBox="0 0 30 30" fill="none" stroke="#fff" stroke-width="2"><rect x="4" y="7" width="22" height="16" rx="2"/><path d="M4 9l11 8 11-8"/></svg></div>
    <h3 class="feature-title">Custom Emails Using Your Domain</h3>
    <ul>
      <li style="margin-bottom:12px">Quickly set up emails for yourself and all your<br>employees with your own domain extension (example –<br>johnd@yoursite.com). No more unprofessional Mailbox<br>and Yondermail email addresses!</li>
      <li>Manage all your business emails from a simple,<br>user-friendly interface!</li>
    </ul>
  </article>
  <article class="feature">
    <div class="feature-icon"><svg width="30" height="30" viewBox="0 0 30 30" fill="none" stroke="#fff" stroke-width="2"><rect x="4" y="5" width="14" height="18" rx="2"/><rect x="13" y="11" width="13" height="14" rx="2"/><path d="M17 20l5-5"/></svg></div>
    <h3 class="feature-title" style="margin-bottom:10px">SEO Service –<br>Automatic Backlink Building</h3>
    <ul>
      <li style="margin-bottom:16px">Let us do the hard work of getting high-quality backlinks<br>to your website. Although difficult to get, backlinks to<br>your website boost search engine ranking more than<br>any other strategy!</li>
      <li>Subscribe now and start getting 10-20 high-quality<br>permanent backlinks to your website every month,<br>guaranteed!</li>
    </ul>
  </article>
  <article class="feature">
    <div class="feature-icon"><svg width="30" height="30" viewBox="0 0 30 30" fill="none" stroke="#fff" stroke-width="2"><circle cx="15" cy="11" r="6"/><rect x="6" y="18" width="18" height="8" rx="2"/></svg></div>
    <h3 class="feature-title">Customer Relationship<br>Management (CRM) System</h3>
    <ul>
      <li>Automate the lead follow up process to consistently<br>stay in front of your potential customers!</li>
      <li>Schedule automatic email and text campaigns and<br>effortlessly follow your funnels from lead to closing!</li>
    </ul>
  </article>
</section>

<section class="tools">
  <svg class="tools-notch" width="100" height="28" viewBox="0 0 100 28" aria-hidden="true"><polygon points="0,0 100,0 56,26" fill="#ffffff"/></svg>
  <h2 class="section-heading" style="top:52px">More Tools to Help You <b>Grow Your Business</b></h2>
  <nav class="tool-grid">
    <a class="tool" href="https://pavlora.com">Get Your LLC</a>
    <a class="tool is-featured" href="https://pavlora.com">Social Media Posting Service</a>
    <a class="tool" href="https://pavlora.com">Patent Application</a>
    <a class="tool" href="https://pavlora.com">Website Design and<br>Maintenance</a>
    <a class="tool" href="https://pavlora.com">Logo Design</a>
    <a class="tool" href="https://pavlora.com">Printing Services<small>(including postcards, flyers, and merch.)</small></a>
    <a class="tool" href="https://pavlora.com">Search Ads Management</a>
    <a class="tool" href="https://pavlora.com">Trademark Registration</a>
    <a class="tool" href="https://pavlora.com">Bulk AI Content<br>Generator</a>
  </nav>
</section>

<footer class="site-footer">
  <div class="brand"><span class="brand-dot"></span>Pavlora</div>
  <p class="copyright">© 2024 Pavlora. All Rights Reserved</p>
  <div class="social" aria-label="Social media links">
    <span></span><span></span><span></span><span></span><span></span>
    <span></span><span></span><span></span><span></span><span></span>
  </div>
</footer>

</body>
</html>
```